Website for Torvel Capital - investment banking firm

We have a corporate identity (thanks to Ravinka/31842) and want to extend that into a website design.  See the attached zipped files.
We have software folks in-house to do the coding.
See the attached Project Brief & Notes for more details.  Don't worry about the actual text - lorem ipsum will be fine.
The server will be Apache.
Thank you!
Desmond

Industry/Entity Type
Investment

```html
<!DOCTYPE html>
<html lang="en">
<head>
<meta charset="utf-8">
<title>Torvel Capital</title>
<link href="https://fonts.googleapis.com/css2?family=Open+Sans:wght@400;600&display=swap" rel="stylesheet">
<style>
:root{
  --brand:#1f4f9c;
  --brand-dark:#1a428a;
  --nav-active:#9b9ea4;
  --ink:#222;
  --muted:#444;
  --panel:#ececec;
  --band:#f6f6f6;
  --line:#e3e3e3;
  --footer:#30343e;
  --footer-bottom:#3a3c40;
  --footer-text:#c9ccd2;
}
*{box-sizing:border-box;margin:0;padding:0}
html,body{width:739px;height:1200px;overflow:hidden}
body{position:relative;background:#fff;font-family:"Open Sans",Arial,sans-serif;color:var(--ink)}
.abs{position:absolute}

/* header */
.brand{left:106px;top:20px;display:flex;align-items:center;gap:8px}
.brand-dot{width:26px;height:26px;border-radius:50%;background:var(--brand)}
.brand-name{font-size:18px;font-weight:600;color:var(--brand);letter-spacing:.5px}
.search{left:519px;top:27px;width:115px;height:19px;border:1px solid #c9c9c9;border-radius:2px;font-size:7px;font-style:italic;color:#999;padding:3px 5px}
.search svg{position:absolute;right:4px;top:3px}

/* nav */
.nav{left:0;top:72px;width:739px;height:30px;background:var(--brand);display:flex;padding-left:106px}
.nav a{display:block;color:#fff;text-decoration:none;font-size:8.3px;line-height:30px;padding:0 13px;border-right:1px solid #2a5aa8}
.nav a.active{background:var(--nav-active);padding:0 14px}

/* hero */
.hero{left:0;top:102px;width:739px;height:283px;background:linear-gradient(120deg,#8d8f93 0%,#b9babd 35%,#d9d9da 55%,#9c9ea2 100%)}
.hero-arrow{top:240px;width:26px;height:26px;border-radius:50%;background:rgba(90,90,90,.45);display:flex;align-items:center;justify-content:center}

/* services */
.services{left:0;top:385px;width:739px;height:166px;background:var(--band);border-bottom:1px solid var(--line)}
.service{width:130px;text-align:center;top:18px}
.service-icon{width:66px;height:66px;margin:0 auto;border-radius:50%;background:radial-gradient(circle at 50% 40%,#fff 0%,#ececec 70%,#d8d8d8 100%);border:2px solid #fff;box-shadow:0 0 0 1px #ddd;display:flex;align-items:center;justify-content:center}
.service h3{font-size:8.6px;font-weight:400;margin-top:16px}
.service p{font-size:6px;line-height:11.5px;color:var(--muted);margin-top:5px}

/* welcome */
.welcome{left:106px;top:568px;width:527px;text-align:center}
.welcome h2{font-size:9.6px;font-weight:600}
.welcome h2 span{color:var(--brand);font-weight:400}
.welcome p{font-size:6px;line-height:11.6px;color:var(--muted);margin-top:10px}

/* feature cards */
.card{top:648px;width:164px;height:240px;background:var(--panel);text-align:center}
.card-img{margin:6px auto 0;width:148px;height:109px}
.card h3{font-size:9px;font-weight:400;margin-top:14px}
.card p{font-size:6px;line-height:11.6px;color:var(--muted);margin:9px 10px 0}
.btn{position:absolute;left:56px;top:212px;width:48px;height:19px;border-radius:10px;background:var(--brand);color:#fff;font-size:6px;line-height:19px;font-weight:600}

/* team */
.team{left:468px;top:645px;width:166px}
.team h2{font-size:9.6px;font-weight:400;color:var(--brand);padding-bottom:8px;border-bottom:1px solid var(--line)}
.member{position:absolute;left:2px;display:flex;gap:12px;width:164px}
.member-img{width:56px;height:58px;flex:none;border:2px solid #fff;box-shadow:0 0 0 1px #ddd}
.member h4{font-size:7px;font-weight:400;margin-top:0}
.member p{font-size:5.6px;line-height:11px;color:var(--muted);margin-top:6px;text-align:justify}

/* clients */
.clients-title{left:106px;top:909px;font-size:9.6px;color:var(--brand)}
.clients{left:105px;top:934px;width:529px;height:52px;border:1px solid var(--line);display:flex;align-items:center;justify-content:space-around;padding:0 8px}
.client{display:flex;align-items:center;gap:5px;font-size:11px;color:#b9b9b9}
.client i{display:block;width:14px;height:14px;border-radius:50%;background:#d0d0d0}

/* footer */
.footer{left:0;top:1008px;width:739px;height:156px;background:var(--footer)}
.footer h5{position:absolute;top:18px;font-size:9px;font-weight:400;color:var(--footer-text);letter-spacing:.2px}
.map{left:107px;top:44px;width:148px;height:82px;border:3px solid #fff;border-radius:3px;background:linear-gradient(135deg,#e8e6df,#d9dccf)}
.contact{left:278px;font-size:7px;line-height:12px;color:var(--footer-text);display:flex;gap:10px}
.contact svg{flex:none}
.newsletter p{position:absolute;left:472px;top:52px;width:165px;font-size:6px;line-height:11.5px;color:var(--footer-text)}
.email-input{left:472px;top:92px;width:116px;height:26px;background:#fff;font-size:6px;line-height:26px;padding-left:6px;color:#333}
.signup{left:588px;top:92px;width:46px;height:26px;background:var(--brand);color:#fff;font-size:9.6px;line-height:26px;text-align:center}
.copyright{left:0;top:1164px;width:739px;height:36px;background:var(--footer-bottom);color:#fff;font-size:6.4px;font-weight:600;text-align:center;line-height:36px}
</style>
</head>
<body>

<header>
  <div class="abs brand"><span class="brand-dot"></span><span class="brand-name">TORVEL CAPITAL</span></div>
  <div class="abs search">Search
    <svg width="11" height="11" viewBox="0 0 11 11"><circle cx="4.5" cy="4.5" r="3.2" fill="none" stroke="#1f4f9c" stroke-width="1.5"/><path d="M7 7l3 3" stroke="#1f4f9c" stroke-width="2"/></svg>
  </div>
</header>

<nav class="abs nav">
  <a class="active" href="#">Home</a>
  <a href="#">About Us</a>
  <a href="#">Services</a>
  <a href="#">Current Engagements</a>
  <a href="#">Completed Transactions</a>
  <a href="#">Contact Us</a>
</nav>

<section class="abs hero" role="img" aria-label="Businessman pointing at a sketched rising bar chart with a red trend line">
  <div class="abs hero-arrow" style="left:30px;top:138px"><svg width="8" height="8" viewBox="0 0 8 8"><path d="M5 1L2 4l3 3" fill="none" stroke="#fff" stroke-width="1.4"/></svg></div>
  <div class="abs hero-arrow" style="left:687px;top:138px"><svg width="8" height="8" viewBox="0 0 8 8"><path d="M3 1l3 3-3 3" fill="none" stroke="#fff" stroke-width="1.4"/></svg></div>
</section>

<section class="abs services">
  <div class="abs service" style="left:104px">
    <div class="service-icon"><svg width="30" height="30" viewBox="0 0 30 30"><circle cx="12" cy="9" r="6" fill="#111"/><path d="M2 27c0-7 4-11 10-11s9 3 10 6v5z" fill="#111"/><path d="M23 17v9M18.5 21.5h9" stroke="#111" stroke-width="2.6"/></svg></div>
    <h3>Strategic Advisory Services</h3>
    <p>Torvel Capital has a diverse array of clients ranging from multi-billion dollar strategic acquirers to large private</p>
  </div>
  <div class="abs service" style="left:239px">
    <div class="service-icon"><svg width="30" height="30" viewBox="0 0 30 30"><circle cx="15" cy="15" r="13" fill="#111"/><circle cx="15" cy="15" r="8" fill="#fff"/><circle cx="15" cy="15" r="4.5" fill="#111"/></svg></div>
    <h3>Current Engagements</h3>
    <p>Torvel Capital has a diverse array of clients ranging from multi-billion dollar strategic acquirers to large private</p>
  </div>
  <div class="abs service" style="left:373px">
    <div class="service-icon"><svg width="36" height="30" viewBox="0 0 36 30"><path d="M14 4a11 11 0 1 0 9 17" fill="none" stroke="#111" stroke-width="2.4"/><circle cx="14" cy="15" r="5.5" fill="none" stroke="#111" stroke-width="3.5" stroke-dasharray="3 2"/><circle cx="14" cy="15" r="2" fill="#111"/><path d="M22 15h8" stroke="#111" stroke-width="2.4"/><path d="M29 11l4 4-4 4z" fill="#111"/></svg></div>
    <h3>Completed Transactions</h3>
    <p>Torvel Capital has a diverse array of clients ranging from multi-billion dollar strategic acquirers to large private</p>
  </div>
  <div class="abs service" style="left:508px">
    <div class="service-icon"><svg width="34" height="34" viewBox="0 0 34 34"><circle cx="12" cy="13" r="6" fill="none" stroke="#111" stroke-width="4" stroke-dasharray="3 2.2"/><circle cx="24" cy="8" r="3.5" fill="none" stroke="#111" stroke-width="2.6" stroke-dasharray="2 1.6"/><circle cx="17" cy="26" r="3.5" fill="none" stroke="#111" stroke-width="2.6" stroke-dasharray="2 1.6"/></svg></div>
    <h3>Regulatory Compliance</h3>
    <p>Torvel Capital has a diverse array of clients ranging from multi-billion dollar strategic acquirers to large private</p>
  </div>
</section>

<section class="abs welcome">
  <h2>Welcome To <span>Torvel</span></h2>
  <p>Torvel Capital is an independent investment bank working for buyers in a number of industries. We utilize exceptional technology in finding companies to meet our client's search criteria. We will not waste a buyer's time, a seller's time, or our own time. Torvel Capital is an independent investment bank working for buyers in a number of industries. We utilize exceptional technology in finding companies to meet our client's search criteria. We will not waste a buyer's time, a seller's time, or our own time.</p>
</section>

<article class="abs card" style="left:106px">
  <div class="card-img" role="img" aria-label="Business handshake in front of glass office towers" style="background:linear-gradient(160deg,#cfe0ef,#6f8fad 60%,#2d3440)"></div>
  <h3>Who We Are</h3>
  <p>Torvel Capital has a diverse array of clients ranging from multi-billion dollar strategic acquirers to large private equity funds. We will not engage a client as a buyer if we believe there is any</p>
  <span class="btn">Read More</span>
</article>

<article class="abs card" style="left:287px">
  <div class="card-img" role="img" aria-label="Business team applauding in a meeting" style="background:linear-gradient(120deg,#d7dde4,#b6bcc4 50%,#e6dcd4)"></div>
  <h3>Our Process</h3>
  <p>Once we have your acquisition parameters, we feed these into our software to create an initial target list. The criteria used to create this list can include geography, revenue targets, earning</p>
  <span class="btn">Read More</span>
</article>

<aside class="abs team">
  <h2>Our &nbsp;Teams</h2>
  <div class="member" style="top:39px">
    <div class="member-img" role="img" aria-label="Portrait of a smiling team member" style="background:linear-gradient(#e8e8e8,#b9b1aa)"></div>
    <div><h4>Experienced professionals</h4><p>Torvel Capital's team of bankers and advisors is comprised of experienced professionals. Our research team is critical in</p></div>
  </div>
  <div class="member" style="top:111px">
    <div class="member-img" role="img" aria-label="Advisor on a phone call at a desk" style="background:linear-gradient(#b7d4e6,#eef3f6)"></div>
    <div><h4>Supported by expert re</h4><p>Torvel Capital's team of bankers and advisors is comprised of experienced professionals. Our research team is critical in</p></div>
  </div>
  <div class="member" style="top:183px">
    <div class="member-img" role="img" aria-label="Team member holding documents" style="background:linear-gradient(135deg,#6fb7b3,#e9eef0)"></div>
    <div><h4>Team and sophisticated</h4><p>Torvel Capital's team of bankers and advisors is comprised of experienced professionals. Our research team is critical in</p></div>
  </div>
</aside>

<h2 class="abs clients-title" style="font-weight:400">Our clients</h2>
<div class="abs clients">
  <span class="client">Brickline</span>
  <span class="client"><i></i>Orbita</span>
  <span class="client">Vantage</span>
  <span class="client">Amberfield</span>
  <span class="client"><i></i>Northway</span>
</div>

<footer class="abs footer">
  <h5 style="left:107px">GET IN TOUCH</h5>
  <div class="abs map" role="img" aria-label="Street map showing the office location"></div>
  <div class="abs contact" style="top:49px">
    <svg width="10" height="14" viewBox="0 0 10 14"><path d="M5 0a5 5 0 0 0-5 5c0 4 5 9 5 9s5-5 5-9a5 5 0 0 0-5-5z" fill="#15171c"/><circle cx="5" cy="5" r="2" fill="#30343e"/></svg>
    <span>Hong &nbsp;Kong: &nbsp;Suite &nbsp;1804 &nbsp;Harbourline<br>Tower 12 - 18 Kestrel Road West<br>Eastbay, Hong Kong</span>
  </div>
  <div class="abs contact" style="top:88px">
    <svg width="10" height="16" viewBox="0 0 10 16"><rect x="1" y="0.5" width="8" height="15" rx="1.5" fill="none" stroke="#15171c" stroke-width="1.4"/><rect x="2.5" y="2.5" width="5" height="9" fill="#15171c"/></svg>
    <span style="line-height:16px">Call us: 555-310-4826</span>
  </div>
  <div class="abs contact" style="top:116px">
    <svg width="13" height="10" viewBox="0 0 13 10"><rect width="13" height="10" fill="#15171c"/><path d="M0 0l6.5 5L13 0" fill="none" stroke="#30343e" stroke-width="1.2"/></svg>
    <span>info@torvelcapital.com</span>
  </div>
  <div class="newsletter">
    <h5 style="left:472px">NEWSLETTER</h5>
    <p>Excepteur sint occaecat cupidatat non proident, sunt in culpa qui officia deserunt mollit anim id est laborum.</p>
  </div>
  <div class="abs email-input">Enter Email</div>
  <div class="abs signup">Sign Up</div>
</footer>

<div class="abs copyright">Copyright@2014 Torvel Capital. All Right Reserved</div>

</body>
</html>
```